New Business Card

Need new business cards like attached. if possible add QR code. Vertical Business Card

I need creative and unique business card design using my company logo. Ok to change logo color. We are a small brokerage doing both Real Estate and Mortgage services. Need to have the follow on business card;
1. agent name - Nola Brenner - Realtor
2. cell - 949-555-2146
3. license number - DRE 07461392
4. business name - Tallow Ridge Realty & Lending, Inc
5. business office - 626-555-4817
6. business address - 482 W. Larkmoor Ave #212, Arcadia CA 91006
7. business logo - attached (ok to use different color on logo)

```html
<!DOCTYPE html>
<html lang="en">
<head>
<meta charset="utf-8">
<title>Tallow Ridge Realty &amp; Lending – Business Card</title>
<link rel="stylesheet" href="https://fonts.googleapis.com/css2?family=Montserrat:wght@300;400;600;700&display=swap">
<style>
  :root {
    --stage: #2b2b2d;
    --card: #19191b;
    --card-edge: #0f0f10;
    --blue: #2f7fd6;
    --blue-light: #4aa9e6;
    --blue-deep: #1d4fb0;
    --white: #e9e9ea;
    --pattern-light: #6d6f73;
    --pattern-dark: #0c0c0d;
  }
  * { margin: 0; padding: 0; box-sizing: border-box; }
  html, body { width: 1200px; height: 1129px; overflow: hidden; }
  body {
    background: var(--stage);
    font-family: "Montserrat", sans-serif;
    position: relative;
  }
  .card {
    position: absolute;
    top: 185px;
    width: 420px;
    height: 760px;
    background: var(--card);
    border: 1px solid var(--card-edge);
    box-shadow: 0 18px 40px rgba(0,0,0,.45);
  }
  .card--back { left: 140px; padding: 22px; }
  .card--front { left: 640px; }

  .back-pattern {
    width: 100%;
    height: 100%;
    background: linear-gradient(160deg, var(--pattern-light) 0%, #3a3b3e 45%, var(--pattern-dark) 100%);
  }
  .back-accent {
    position: absolute;
    top: 120px;
    right: 70px;
    width: 56px;
    height: 56px;
    background: linear-gradient(135deg, var(--blue-deep), var(--blue-light));
  }

  .brand {
    position: absolute;
    left: 58px;
    top: 70px;
    width: 304px;
  }
  .brand-square {
    width: 150px;
    height: 150px;
    background: linear-gradient(135deg, var(--blue-deep), var(--blue-light));
    margin-bottom: 30px;
  }
  .brand-name {
    color: var(--blue);
    font-weight: 400;
    font-size: 30px;
    letter-spacing: 9px;
    line-height: 1.15;
    text-transform: uppercase;
  }
  .brand-sub {
    color: var(--blue);
    font-weight: 400;
    font-size: 13px;
    letter-spacing: 4.4px;
    text-transform: uppercase;
    margin-top: 8px;
  }

  .details {
    position: absolute;
    left: 58px;
    top: 420px;
    width: 320px;
    color: var(--white);
    font-weight: 300;
    font-size: 15.5px;
    line-height: 1.35;
  }
  .agent-name {
    color: var(--blue);
    font-weight: 700;
    font-size: 25px;
    text-transform: uppercase;
    line-height: 1.1;
  }
  .agent-role { font-size: 19px; font-weight: 400; margin-bottom: 26px; }
  .company { color: var(--blue); }
  .address { margin-bottom: 24px; }
  .phones { margin-bottom: 22px; }
  .label { color: var(--blue); }
</style>
</head>
<body>
  <section class="card card--back">
    <div class="back-pattern" role="img" aria-label="Repeating grid of embossed brand tiles fading from silver to black"></div>
    <div class="back-accent"></div>
  </section>

  <section class="card card--front">
    <div class="brand">
      <div class="brand-square"></div>
      <div class="brand-name">Tallow Ridge</div>
      <div class="brand-sub">Realty &amp; Lending, Inc</div>
    </div>

    <div class="details">
      <div class="agent-name">Nola Brenner</div>
      <div class="agent-role">Realtor</div>
      <div class="company">Tallow Ridge Realty &amp; Lending, Inc</div>
      <div class="address">482 W. Larkmoor Ave #212,<br>Arcadia CA 91006</div>
      <div class="phones">
        <div><span class="label">M :</span> 949-555-2146</div>
        <div><span class="label">T :</span> 626-555-4817</div>
      </div>
      <div><span class="label">LIC :</span> DRE 07461392</div>
    </div>
  </section>
</body>
</html>
```